Timber Crest Construction Needs business card

Hey we are in need of business card designs. I have upload our logo as a guideline, but free feel to run with it or come up with something unique.
Pls have fun with it and be creative. the name says it all!
i will give some directions after i see a few entries..
Updates
Logo source file has been uploaded..
Hey because of the logo is so colourful already.
Can we have a few submissions with less colour.
Also we are looking for clever/hidden/descriptive business card.

```html
<!DOCTYPE html>
<html lang="en">
<head>
<meta charset="utf-8">
<title>Timber Crest Construction – Business Card</title>
<link rel="stylesheet" href="https://fonts.googleapis.com/css2?family=Open+Sans:wght@400;700&display=swap">
<style>
  :root {
    --backdrop: #e6e6e8;
    --card: #f1f1f1;
    --ink-grey: #5b5d60;
    --ink-dark: #1f2a3a;
    --blue: #2f6fb5;
    --blue-light: #7fb0df;
    --red: #d8282f;
    --yellow: #f3d21c;
    --orange: #e8641e;
    --contact: #f6e23a;
  }
  * { margin: 0; padding: 0; box-sizing: border-box; }
  html, body { width: 1200px; height: 750px; overflow: hidden; }
  body {
    background: radial-gradient(ellipse at 50% 40%, #f4f4f5 0%, var(--backdrop) 75%);
    font-family: "Open Sans", Arial, sans-serif;
    position: relative;
  }
  .card {
    position: absolute;
    width: 520px;
    height: 300px;
    background: var(--card);
    border-radius: 4px;
    overflow: hidden;
    box-shadow: 0 6px 18px rgba(0,0,0,0.14);
  }
  .card--front { left: 80px; top: 90px; }
  .card--back { left: 600px; top: 360px; }
  .card__shapes { position: absolute; inset: 0; width: 100%; height: 100%; }

  .brand {
    position: absolute;
    display: flex;
    align-items: center;
    gap: 10px;
    color: var(--ink-grey);
    font-weight: 700;
  }
  .brand__mark {
    width: 26px; height: 26px;
    background: var(--blue);
  }
  .brand__name { font-size: 27px; letter-spacing: 1px; line-height: 1; text-transform: uppercase; }
  .brand__sub { font-size: 10px; letter-spacing: 3px; text-transform: uppercase; margin-top: 4px; text-align: right; }
  .card--front .brand { left: 110px; top: 80px; }
  .card--back .brand { right: 26px; top: 60px; }
  .card--back .brand__name { font-size: 22px; }
  .card--back .brand__mark { width: 22px; height: 22px; }

  .person { position: absolute; left: 40px; top: 90px; color: var(--ink-dark); }
  .person__name { font-size: 16px; font-weight: 700; }
  .person__title { font-size: 8px; }

  .contact-strip {
    position: absolute; left: 40px; top: 170px;
    width: 22px; height: 110px;
    background: var(--orange);
    display: flex; flex-direction: column; align-items: center; justify-content: space-evenly;
  }
  .contact-strip__dot { width: 10px; height: 10px; background: var(--contact); border-radius: 2px; }

  .contact {
    position: absolute; left: 72px; top: 168px;
    list-style: none;
    color: var(--contact);
    font-size: 11.5px;
    line-height: 14px;
  }
</style>
</head>
<body>

  <section class="card card--front" aria-label="Business card front">
    <svg class="card__shapes" viewBox="0 0 520 300" preserveAspectRatio="none" aria-hidden="true">
      <path d="M0 215 C170 232 340 176 520 84 L520 106 C330 188 150 238 0 238 Z" fill="var(--yellow)"/>
      <path d="M0 238 C150 238 330 188 520 106 L520 121 C330 201 150 251 0 251 Z" fill="var(--red)"/>
      <path d="M0 251 C150 251 330 201 520 121 L520 300 L0 300 Z" fill="var(--blue)"/>
    </svg>
    <div class="brand">
      <span class="brand__mark"></span>
      <div>
        <div class="brand__name">Timber Crest</div>
        <div class="brand__sub">Construction</div>
      </div>
    </div>
  </section>

  <section class="card card--back" aria-label="Business card back">
    <svg class="card__shapes" viewBox="0 0 520 300" preserveAspectRatio="none" aria-hidden="true">
      <defs>
        <linearGradient id="panelFill" x1="0" y1="0" x2="1" y2="1">
          <stop offset="0" stop-color="var(--blue-light)"/>
          <stop offset="1" stop-color="var(--blue)"/>
        </linearGradient>
      </defs>
      <path d="M0 0 L150 0 C190 40 200 110 260 132 C330 156 360 210 390 300 L0 300 Z" fill="url(#panelFill)"/>
      <path d="M150 0 C190 40 200 110 260 132 C330 156 360 210 390 300" fill="none" stroke="var(--yellow)" stroke-width="2.5"/>
    </svg>
    <div class="brand">
      <span class="brand__mark"></span>
      <div>
        <div class="brand__name">Timber Crest</div>
        <div class="brand__sub">Construction</div>
      </div>
    </div>
    <div class="person">
      <div class="person__name">Your Name</div>
      <div class="person__title">Job Title</div>
    </div>
    <div class="contact-strip" aria-hidden="true">
      <span class="contact-strip__dot"></span>
      <span class="contact-strip__dot"></span>
      <span class="contact-strip__dot"></span>
      <span class="contact-strip__dot"></span>
      <span class="contact-strip__dot"></span>
    </div>
    <ul class="contact">
      <li>0: 123456789</li>
      <li>0: 123456789</li>
      <li>yourname@website.com</li>
      <li>1234 A Your Adress,</li>
      <li>City, State 123456</li>
      <li>/facebookpage</li>
      <li>@twitteradress</li>
    </ul>
  </section>

</body>
</html>
```